Business Landing Page for SEO Company

Need the landing page of the website designed - I will provide the copy, will need to include details of my company and the services offered, about us, testimonials, faq, etc., and all these elements will need to be arranged graphically on the page.

I want something similar to this: https://torvanequill.com/

Not in terms of color or theme or anything, but we offer a similar service and want to display similar information.

Th services we provide are:

Premium Links
Monthly Links Subscription
Link Insertions

Need to advertise them on the front page. Additionally need a place for testimonials, company details, etc.,

We already have logo for the website. Please use the attached file to insert the logo within the overal design.

Target Market(s)

SEO marketers and agencies

Number of Pages Required

1 page

```html
<!DOCTYPE html>
<html lang="en">
<head>
<meta charset="utf-8">
<title>Linkora — SEO Company</title>
<link href="https://fonts.googleapis.com/css2?family=Poppins:ital,wght@0,400;0,500;0,600;0,700;0,800;1,400&display=swap" rel="stylesheet">
<style>
:root{
  --blue:#2576e0;
  --orange:#ff6a0d;
  --ink:#1d1d1f;
  --grey:#8a8f98;
  --faint:#eeeff1;
  --navy:#0f1829;
  --hero:#1c1f26;
  --white:#ffffff;
}
*{margin:0;padding:0;box-sizing:border-box}
html,body{width:1200px;height:4096px;overflow:hidden;background:var(--white);font-family:'Poppins',sans-serif;color:var(--ink)}
.page{position:relative;width:1200px;height:4096px;overflow:hidden}
.abs{position:absolute}

/* header / hero */
.hero-photo{left:0;top:0;width:1200px;height:660px;background:radial-gradient(ellipse at 70% 40%,#4a4d55 0%,#2a2d34 45%,#15171c 100%)}
.hero-cut{left:0;top:0;width:1200px;height:700px}
.brand{font-weight:600;color:var(--blue);font-size:52px;line-height:1;letter-spacing:-1px}
.header-brand{left:143px;top:36px}
.nav{right:145px;top:52px;display:flex;gap:26px;font-size:15px;color:var(--white)}
.nav a{color:inherit;text-decoration:none;padding-bottom:8px}
.nav a.active{border-bottom:2px solid var(--orange)}
.hero-title{left:0;width:1200px;top:210px;text-align:center;font-size:136px;font-weight:700;color:var(--white);line-height:1;letter-spacing:-2px}
.hero-sub{left:0;width:1200px;top:392px;text-align:center;font-size:31px;font-weight:700;color:var(--white)}
.dots{left:1126px;top:312px;display:flex;flex-direction:column;gap:10px}
.dots i{width:7px;height:7px;border-radius:50%;background:var(--white);display:block}
.dots i.on{background:var(--orange)}

/* services */
.card{top:551px;width:251px;height:391px;border-radius:12px;color:var(--white);text-align:center;padding:30px 22px 0}
.card.blue{background:var(--blue)}
.card.orange{background:var(--orange)}
.card svg{display:block;margin:0 auto}
.card h3{font-size:20px;font-weight:600;line-height:1.45;margin-top:22px}
.card p{font-size:12px;line-height:24px;margin-top:14px}
.card .btn{display:inline-block;margin-top:20px;background:var(--white);border-radius:20px;font-size:11px;font-weight:700;padding:10px 22px}
.card.blue .btn{color:var(--blue)}
.card.orange .btn{color:var(--orange)}

/* about */
.about-vert{left:24px;top:1060px;width:88px;height:420px}
.about-title{left:170px;top:1052px;font-size:62px;font-weight:700;line-height:64px;color:var(--ink)}
.rule{height:3px;width:44px;background:var(--blue)}
.about-copy{left:496px;top:1054px;width:535px;font-size:14.5px;line-height:27px;color:var(--grey)}
.about-copy p+p{margin-top:27px}
.pill{display:flex;align-items:center;justify-content:center;background:var(--orange);color:var(--white);font-weight:600;font-size:16px;border-radius:26px}

/* section heads */
.ghost{left:0;width:1200px;text-align:center;font-weight:800;color:var(--faint);line-height:1;letter-spacing:2px}
.head{left:0;width:1200px;text-align:center;font-weight:600;color:var(--ink);line-height:1}

/* testimonials */
.review{width:270px}
.avatar{width:86px;height:86px;border-radius:50%}
.review p{margin-top:24px;font-size:13px;line-height:24px;font-style:italic;color:var(--grey)}
.review .who{margin-top:18px;font-size:15px;font-weight:700;color:var(--blue);display:flex;align-items:center;gap:14px}
.stars{color:var(--orange);font-size:15px;letter-spacing:1px}

/* faq */
.faq{left:296px;width:607px;height:50px;border-radius:25px;background:var(--white);box-shadow:0 4px 14px rgba(0,0,0,.09);display:flex;align-items:center;justify-content:space-between;padding:0 6px 0 34px;font-size:15px;color:var(--ink)}
.faq .tog{width:36px;height:36px;border-radius:50%;color:var(--white);font-size:22px;font-weight:600;display:flex;align-items:center;justify-content:center}
.tog.open{background:var(--orange)}
.tog.closed{background:var(--blue)}
.faq-answer{left:322px;top:3098px;width:560px;font-size:11.5px;line-height:24px;color:#a2a6ad}

/* footer */
.foot-bg{left:0;top:3500px;width:1200px;height:596px}
.foot-brand{left:148px;top:3752px;font-size:74px}
.social{left:148px;top:3869px;display:flex;gap:9px}
.social span{width:41px;height:41px;border:1.5px solid var(--white);border-radius:50%;display:block}
.foot-h{font-size:19px;font-weight:600;color:var(--white)}
.links{left:486px;top:3736px}
.links ul{list-style:none;margin-top:14px}
.links li{font-size:13px;line-height:27px;color:var(--white)}
.news{left:707px;top:3736px;width:343px}
.news p{margin-top:16px;font-size:13px;color:var(--white)}
.news .field{margin-top:26px;height:40px;border:1px solid #4a5263;border-radius:20px;font-size:11px;color:var(--white);padding:0 28px;display:flex;align-items:center}
.news .pill{margin-top:18px;height:40px;font-size:13px}
.copyright{left:0;width:1200px;top:4022px;text-align:center;font-size:12px;color:var(--white)}
.ghost-foot{left:20px;top:3960px;font-size:130px;font-weight:800;color:rgba(255,255,255,.04);line-height:1}
</style>
</head>
<body>
<div class="page">

  <!-- Hero -->
  <div class="abs hero-photo" role="img" aria-label="Photo of hands typing on a laptop keyboard in a dim office"></div>
  <svg class="abs hero-cut" width="1200" height="700" viewBox="0 0 1200 700">
    <polygon points="0,660 938,660 1200,429 1200,700 0,700" fill="#ffffff"/>
    <polyline points="0,655 938,655 1200,425" fill="none" stroke="#2576e0" stroke-width="9"/>
  </svg>
  <div class="abs brand header-brand">Linkora</div>
  <nav class="abs nav">
    <a class="active">Home</a><a>Services</a><a>About us</a><a>Testimonials</a><a>Faq</a><a>Contact</a>
  </nav>
  <div class="abs hero-title">Linkora</div>
  <div class="abs hero-sub">We are an SEO company</div>
  <div class="abs dots"><i></i><i class="on"></i><i></i></div>

  <!-- Services -->
  <div class="abs card blue" style="left:143px">
    <svg width="72" height="72" viewBox="0 0 72 72" fill="none" stroke="#fff" stroke-width="2.4">
      <rect x="4" y="6" width="64" height="60" rx="3"/><line x1="4" y1="16" x2="68" y2="16"/>
      <polygon points="22,30 50,30 56,38 36,56 16,38"/><line x1="16" y1="38" x2="56" y2="38"/>
    </svg>
    <h3>Premium Links</h3>
    <p>Lorem ipsum dolor sit consectetur adipiscing elit, sed do eiusmod tempor incididunt ut labore et dolore maguis ipsuspendisse ultrices gravicommodo</p>
    <span class="btn">READ MORE</span>
  </div>
  <div class="abs card orange" style="left:413px">
    <svg width="72" height="72" viewBox="0 0 72 72" fill="none" stroke="#fff" stroke-width="2.4">
      <rect x="10" y="12" width="46" height="44" rx="3"/><line x1="10" y1="22" x2="56" y2="22"/>
      <line x1="20" y1="6" x2="20" y2="16"/><line x1="33" y1="6" x2="33" y2="16"/><line x1="46" y1="6" x2="46" y2="16"/>
      <circle cx="18" cy="52" r="10"/><rect x="40" y="42" width="24" height="24" rx="3"/>
    </svg>
    <h3>Monthly Links<br>Subscription</h3>
    <p>Lorem ipsum dolor sit consectetur adipiscing elit, sed do eiusmod tempor incididunt ut labore et dolore maguis ipsuspendisse</p>
    <span class="btn">READ MORE</span>
  </div>
  <div class="abs card blue" style="left:683px">
    <svg width="72" height="72" viewBox="0 0 72 72" fill="none" stroke="#fff" stroke-width="2.4">
      <rect x="6" y="4" width="60" height="54" rx="3"/><line x1="6" y1="14" x2="66" y2="14"/>
      <polyline points="26,34 36,24 46,34"/><line x1="36" y1="24" x2="36" y2="48"/>
      <line x1="24" y1="66" x2="48" y2="66"/><line x1="36" y1="58" x2="36" y2="66"/>
    </svg>
    <h3>Link Insertions</h3>
    <p>Lorem ipsum dolor sit consectetur adipiscing elit, sed do eiusmod tempor incididunt ut labore et dolore maguis ipsuspendisse ultrices gravicommodo</p>
    <span class="btn">READ MORE</span>
  </div>

  <!-- About -->
  <svg class="abs about-vert" viewBox="0 0 88 420" aria-hidden="true">
    <text x="0" y="0" transform="translate(82,420) rotate(-90)" font-family="Poppins, sans-serif" font-weight="800" font-size="112" fill="#eeeff1">ABOUT</text>
  </svg>
  <h2 class="abs about-title">ABOUT<br>LINKORA</h2>
  <div class="abs rule" style="left:170px;top:1214px"></div>
  <div class="abs about-copy">
    <p>Lorem ipsum dolor sit amet, consectetur adipiscing elit, sed do eiusmod tempor incididunt ut labore et dolore magn suspendisse ultrices gravida. Risus commodo viverra maecenas accumsan lacus vel facilisis. Lorem ipsum dolor sit amet, consectetur adipiscing elit, sed do eiusmod tempor incididunt ut labore et dolore magn suspendisse ultrices gravida. Risus commodo viverra maecenas accumsan lacus vel facilisirem ipsum dolor sit amet, consectetur adipiscing elit, sed do eiusmod tempor incididunt ut labore et dolore magn suspendisse ultrices gravisus commodo viverra maecenas accumsan la accumsan lacus vecus vel facilisis.</p>
    <p>Lorem ipsum dolor sit amet, consectetur adipiscing elit, sed do eiusmod tempor incididunt ut labore et dolore magn suspendisse ultrices gravida. Risus commodo viverra maecenas accumsan lacus vel facilisis. Lorem ipsum dolor sit amet, consectetur adipiscing elit, sed do eiusmod tempor incididunt ut labore et dolore magn suspendisse ultrices gravida</p>
  </div>
  <div class="abs pill" style="left:496px;top:1507px;width:149px;height:51px">READ MORE</div>

  <!-- Testimonials -->
  <div class="abs ghost" style="top:1688px;font-size:112px">TESTIMONIALS</div>
  <h2 class="abs head" style="top:1732px;font-size:60px">TESTIMONIALS</h2>
  <div class="abs rule" style="left:578px;top:1818px"></div>

  <div class="abs review" style="left:140px;top:1928px">
    <div class="avatar" role="img" aria-label="Portrait of a client" style="background:#8b7a6e"></div>
    <p>Lorem ipsum dolor sit amet, consectetur adipiscind do eiusmod tempor incididunt ut labore et dolore magna aliquauis ipsum suspendisse ultrices gravidasuommodo viverra maumsan lacgravidasuommodo viverra maumsanusus vel facilisis.</p>
    <div class="who">– ARLO VENN <span class="stars">★★★★★</span></div>
  </div>
  <div class="abs review" style="left:466px;top:1928px">
    <div class="avatar" role="img" aria-label="Portrait of a client" style="background:#5b4a44"></div>
    <p>Lorem ipsum dolor sit amet, consectetur adipiscind do eiusmod tempor incididunt ut labore et dolore magna aliquauis ipsum suspendisse ultrices gravidasuommodo viverra maumsan lacgravidasuommodo viverra maumsanusus vel facilisis.</p>
    <div class="who">– MIRA CASTELL <span class="stars">★★★★★</span></div>
  </div>
  <div class="abs review" style="left:792px;top:1928px">
    <div class="avatar" role="img" aria-label="Portrait of a client" style="background:#6c88a4"></div>
    <p>Lorem ipsum dolor sit amet, consectetur adipiscind do eiusmod tempor incididunt ut labore et dolore magna aliquauis ipsum suspendisse ultrices gravidasuommodo viverra maumsan lacgravidasuommodo viverra maumsanusus vel facilisis.</p>
    <div class="who">– TOBIN ASHE <span class="stars">★★★★★</span></div>
  </div>
  <div class="abs review" style="left:140px;top:2289px">
    <div class="avatar" role="img" aria-label="Portrait of a client" style="background:#3a4048"></div>
    <p>Lorem ipsum dolor sit amet, consectetur adipiscind do eiusmod tempor incididunt ut labore et dolore magna aliquauis ipsum suspendisse ultrices gravidasuommodo viverra maumsan lacgravidasuommodo viverra maumsanusus vel facilisis.</p>
    <div class="who">– ROWAN PIKE <span class="stars">★★★★★</span></div>
  </div>
  <div class="abs review" style="left:466px;top:2289px">
    <div class="avatar" role="img" aria-label="Portrait of a client" style="background:#e8b48e"></div>
    <p>Lorem ipsum dolor sit amet, consectetur adipiscind do eiusmod tempor incididunt ut labore et dolore magna aliquauis ipsum suspendisse ultrices gravidasuommodo viverra maumsan lacgravidasuommodo viverra maumsanusus vel facilisis.</p>
    <div class="who">– DARIO FENN <span class="stars">★★★★★</span></div>
  </div>
  <div class="abs review" style="left:792px;top:2289px">
    <div class="avatar" role="img" aria-label="Portrait of a client" style="background:#9a8f8a"></div>
    <p>Lorem ipsum dolor sit amet, consectetur adipiscind do eiusmod tempor incididunt ut labore et dolore magna aliquauis ipsum suspendisse ultrices gravidasuommodo viverra maumsan lacgravidasuommodo viverra maumsanusus vel facilisis.</p>
    <div class="who">– LENA SORREL <span class="stars">★★★★★</span></div>
  </div>
  <div class="abs pill" style="left:526px;top:2650px;width:148px;height:50px">VIEW MORE</div>

  <!-- FAQ -->
  <div class="abs ghost" style="top:2838px;font-size:112px">QUESTIONS</div>
  <h2 class="abs head" style="top:2882px;font-size:60px;letter-spacing:4px">FAQ</h2>
  <div class="abs rule" style="left:578px;top:2968px"></div>

  <div class="abs faq" style="top:3030px"><span>Lorem ipsum dolor sit ametconsectetur adipiscing elit?</span><span class="tog open">–</span></div>
  <p class="abs faq-answer">Lorem ipsum dolor sit amet, consectetur adipiscing elit, sed do eiusmod tempor incididunt ut labore et dolore magna aliqua. Ut enim ad minim veniam, quis nostrud exercitation ullamco laboris nisi ut aliquip ex lor in reprehenderit in voluptate velit esse</p>
  <div class="abs faq" style="top:3179px"><span>Sed ut perspiciatis unde omnis iste natus error sit?</span><span class="tog closed">+</span></div>
  <div class="abs faq" style="top:3241px"><span>Iunde omnis iste natus error sit voluptatem accusantium ?</span><span class="tog closed">+</span></div>
  <div class="abs faq" style="top:3303px"><span>Lorem ipsum dolor sit ametconsectetur adipiscing elit?</span><span class="tog closed">+</span></div>
  <div class="abs faq" style="top:3365px"><span>Iunde omnis iste natus error sit voluptatem accusantium ?</span><span class="tog closed">+</span></div>

  <!-- Footer -->
  <svg class="abs foot-bg" width="1200" height="596" viewBox="0 0 1200 596" role="img" aria-label="Dark navy footer background with a faint digital particle texture">
    <polygon points="254,20 1200,20 1200,596 0,596 0,230" fill="#0f1829"/>
    <polyline points="0,228 254,18 1200,18" fill="none" stroke="#2576e0" stroke-width="8"/>
  </svg>
  <div class="abs ghost-foot">CONTACT</div>
  <div class="abs brand foot-brand">Linkora</div>
  <div class="abs social"><span></span><span></span><span></span><span></span><span></span></div>
  <div class="abs links">
    <div class="foot-h">QUICK LINKS</div>
    <ul><li>Home</li><li>Services</li><li>About us</li><li>Testimonials</li><li>Faq</li><li>Contact</li></ul>
  </div>
  <div class="abs news">
    <div class="foot-h">SIGN UP NEWSLETTER</div>
    <p>Lorem ipsum dolor sit ametconsectetur adipiscin</p>
    <div class="field">Enter Email</div>
    <div class="pill">SIGN UP</div>
  </div>
  <div class="abs copyright">© 2021 - Linkora.All Rights Reserved &nbsp;|&nbsp; Privacy Policy &nbsp;|&nbsp; Terms and Use</div>

</div>
</body>
</html>
```